Enhance Landing Page

Actual: https://thecoralparlor.com/aplique-no-litoral-lp-port/

I need a better design for this page:
Using this shortcodes : https://bolder.qrxlayouts.net
Rules:
. Keep the page header
. Keep the footer

```html
<!DOCTYPE html>
<html lang="en">
<head>
<meta charset="utf-8">
<title>Coral Parlor — Invest in Florida</title>
<link rel="stylesheet" href="https://fonts.googleapis.com/css2?family=Montserrat:wght@400;600;700;800&family=Open+Sans:wght@400;600;700&display=swap">
<style>
:root{
  --purple:#3c2c7c;
  --purple-deep:#2b2260;
  --violet:#6c3a92;
  --orange:#f7931e;
  --orange-dark:#ec7a12;
  --crimson:#e2063d;
  --green:#1fae4b;
  --teal:#2aa5b8;
  --ink:#2e2e3a;
  --muted:#666b78;
  --light:#eef0f3;
  --white:#fff;
}
*{box-sizing:border-box;margin:0;padding:0}
html,body{width:1200px;height:4401px;overflow:hidden}
body{font-family:"Open Sans",Arial,sans-serif;color:var(--ink);background:var(--white);position:relative}
.sec{position:absolute;left:0;width:1200px;overflow:hidden}
.btn{position:absolute;display:flex;align-items:center;justify-content:center;font-family:"Montserrat",Arial,sans-serif;font-weight:700;color:#fff;letter-spacing:.5px;text-transform:uppercase}
.btn-orange{background:linear-gradient(180deg,var(--orange),var(--orange-dark))}
.btn-red{background:var(--crimson)}
.ph{position:absolute}

/* header */
.header{top:0;height:88px;background:#fff;z-index:5;overflow:visible}
.logo-tab{position:absolute;left:470px;top:0;width:260px;height:118px;background:#fff;border-radius:0 0 130px 130px}
.brand{position:absolute;text-align:center;font-family:"Montserrat",Arial,sans-serif;font-weight:800;color:var(--crimson);line-height:1}
.header .brand{left:500px;top:24px;width:200px;font-size:30px}
.brand small{display:block;font-size:13px;letter-spacing:6px;margin-top:4px}
.wa{position:absolute;background:var(--green);color:#fff;font:700 12px "Montserrat",sans-serif;display:flex;align-items:center;gap:6px;padding:0 12px;border-radius:3px}
.phones{position:absolute;display:flex;gap:14px;font:600 11px "Open Sans",sans-serif;color:var(--ink)}
.phones span{display:flex;align-items:center;gap:4px}
.dot{width:12px;height:12px;border-radius:50%;display:inline-block}
.cta-icon{position:absolute;display:flex;align-items:center;gap:8px;font:700 11px "Montserrat",sans-serif;color:var(--purple-deep);line-height:1.15;text-transform:uppercase}
.cta-icon i{width:34px;height:34px;border-radius:50%;display:inline-block}

/* hero */
.hero{top:88px;height:590px}
.hero .photo{inset:0;background:linear-gradient(180deg,#3b3a78 0%,#7a5b9a 30%,#d57a8a 55%,#3c2450 75%,#1a1430 100%)}
.hero h1{position:absolute;top:196px;left:0;width:1200px;text-align:center;font:800 44px/1.05 "Montserrat",sans-serif;color:#fff;text-transform:uppercase}
.arrow{position:absolute;width:40px;height:40px}

/* about */
.about{top:675px;height:470px}
.about h2{position:absolute;left:165px;top:74px;font:800 30px/1.2 "Montserrat",sans-serif;color:var(--purple-deep);text-transform:uppercase}
.about p{position:absolute;left:165px;top:158px;width:460px;font-size:15px;line-height:1.6;color:var(--muted)}

/* services */
.services{top:1120px;height:440px}
.services h2,.projects h2{position:absolute;width:1200px;text-align:center;font:800 26px "Montserrat",sans-serif;text-transform:uppercase}
.card{position:absolute;top:145px;width:207px;height:188px;border:2px solid rgba(255,255,255,.55);display:flex;flex-direction:column;align-items:center;justify-content:flex-end;padding-bottom:30px;gap:26px;color:#fff;font:700 15px/1.2 "Montserrat",sans-serif;text-align:center;text-transform:uppercase}
.card svg{width:62px;height:62px}

/* vision */
.vision{top:1546px;height:362px}
.vision h2{position:absolute;top:100px;width:1200px;text-align:center;font:800 36px "Montserrat",sans-serif;color:#fff}
.vision p{position:absolute;top:150px;left:370px;width:460px;text-align:center;font-size:18px;line-height:1.4;color:#fff}

/* projects */
.projects{top:1908px;height:640px}
.tile{position:absolute}
.tile-label{display:flex;flex-direction:column;align-items:center;justify-content:center;color:#fff;font:600 17px "Montserrat",sans-serif;text-transform:uppercase}
.tile-label span{color:var(--orange);font-size:12px;margin-top:6px;font-weight:700}

/* prices */
.prices{top:2548px;height:476px;background:linear-gradient(180deg,#f4f4f6,#e8e9ed)}
.prices h2{position:absolute;left:596px;top:120px;font:800 30px/1.15 "Montserrat",sans-serif;color:var(--purple-deep);text-transform:uppercase}
.prices p{position:absolute;left:596px;top:200px;width:420px;font-size:15px;line-height:1.5;color:var(--muted)}

/* stats */
.stats{top:3022px;height:156px;background:linear-gradient(90deg,var(--crimson),#c8002f)}
.stat{position:absolute;top:40px;color:#fff}
.stat b{display:block;font:800 34px "Montserrat",sans-serif}
.stat span{display:block;font:400 20px/1.1 "Montserrat",sans-serif;text-transform:uppercase;margin-top:2px}

/* builder */
.builder{top:3178px;height:446px}
.builder h2{position:absolute;left:663px;top:110px;font:800 36px "Montserrat",sans-serif;color:var(--crimson);text-transform:uppercase}
.builder p{position:absolute;left:663px;top:172px;width:390px;font-size:15px;line-height:1.55;color:var(--muted)}

/* contact */
.contact{top:3623px;height:470px}
.contact .photo{inset:0;background:linear-gradient(135deg,#4a2e86 0%,#6b3c9a 55%,#7d4aa6 100%)}
.contact .kicker{position:absolute;top:42px;width:1200px;text-align:center;font:400 18px "Montserrat",sans-serif;color:#fff;text-transform:uppercase;letter-spacing:1px}
.contact h2{position:absolute;top:68px;width:1200px;text-align:center;font:800 32px "Montserrat",sans-serif;color:#fff;text-transform:uppercase}
.field{position:absolute;border:1.5px solid rgba(255,255,255,.8);color:#fff;font-size:14px;padding:0 16px;display:flex;align-items:center}
.field.msg{align-items:flex-start;padding-top:12px}

/* footer */
.footer{top:4093px;height:264px;background:var(--light)}
.addr{position:absolute;left:147px;font-size:11px;line-height:1.45;color:var(--ink)}
.addr b{display:flex;align-items:center;gap:6px;font:700 13px "Montserrat",sans-serif;color:var(--purple-deep)}
.pin{width:10px;height:14px}
.footer .brand{left:480px;top:100px;width:240px;font-size:40px}
.footer .brand small{font-size:15px;letter-spacing:8px}
.legal{top:4357px;height:44px;background:#1d1b2a;color:#fff;display:flex;align-items:center;justify-content:space-between;padding:0 147px;font:600 10px "Montserrat",sans-serif;text-transform:uppercase}
.legal nav{display:flex;gap:34px}
</style>
</head>
<body>

<!-- HEADER -->
<header class="sec header">
  <div class="logo-tab"></div>
  <div class="brand">CORAL<small>PARLOR</small></div>
  <div class="wa" style="left:211px;top:28px;height:20px">
    <svg width="12" height="12" viewBox="0 0 12 12"><path d="M3 1.5l2 2-1 1.2a6 6 0 0 0 3.3 3.3L8.5 7l2 2-1 1.5C5.5 10.5 1.5 6.5 1.5 2.5z" fill="#fff"/></svg>
    USA +1 (555) 010-2248
  </div>
  <div class="phones" style="left:165px;top:58px">
    <span><i class="dot" style="background:var(--green)"></i>+55 21 5550-1842</span>
    <span><i class="dot" style="background:var(--purple)"></i>+1 (555) 014-3370</span>
  </div>
  <div class="cta-icon" style="left:769px;top:28px"><i style="background:var(--crimson)"></i>Talk to an<br>agent</div>
  <div class="cta-icon" style="left:913px;top:28px"><i style="background:var(--teal)"></i>Schedule a<br>conversation</div>
</header>

<!-- HERO -->
<section class="sec hero">
  <div class="ph photo" role="img" aria-label="City skyline reflected on a lake at sunset"></div>
  <h1>Invest in Florida and<br>effectively tranquility</h1>
  <div class="btn btn-orange" style="left:515px;top:302px;width:184px;height:44px;font-size:15px">Contact us</div>
  <svg class="arrow" style="left:110px;top:252px" viewBox="0 0 40 40"><path d="M26 8L12 20l14 12M12 20h24" stroke="#fff" stroke-width="3" fill="none"/></svg>
  <svg class="arrow" style="left:1050px;top:252px" viewBox="0 0 40 40"><path d="M14 8l14 12-14 12M28 20H4" stroke="#fff" stroke-width="3" fill="none"/></svg>
  <svg class="ph" style="left:0;bottom:0" width="1200" height="70" viewBox="0 0 1200 70"><path d="M0 70L1200 28V70Z" fill="#fff"/><path d="M760 58L1200 30V6Z" fill="var(--crimson)"/></svg>
</section>

<!-- ABOUT -->
<section class="sec about">
  <h2>Gifts in Brazil and<br>the United States</h2>
  <p>The Coral Parlor has a permanent Lounge in Rio de Janeiro, Brazil and Orlando, Florida. With an innovative concept of 360 ° assistance, advising clients who wish to buy a property in the United States, whether for Investing or Living. With the exclusive partnership of Halvorsen Homes, the largest construction company in the United States, we guarantee the best choices for you and your family!</p>
  <div class="btn btn-orange" style="left:165px;top:345px;width:188px;height:46px;font-size:14px">Learn more</div>
  <svg class="ph" style="left:655px;top:15px" width="380" height="400" viewBox="0 0 380 400">
    <polygon points="140,8 300,40 372,190 320,350 150,392 30,300 8,150" fill="var(--crimson)"/>
    <polygon points="150,22 306,56 366,198 310,346 155,382 40,296 20,160" fill="#6d7a6a" role="img" aria-label="Lounge interior with armchairs and wall art"/>
  </svg>
</section>

<!-- SERVICES -->
<section class="sec services">
  <svg class="ph" style="left:0;top:0" width="1200" height="440" viewBox="0 0 1200 440" preserveAspectRatio="none">
    <defs><linearGradient id="svg-g" x1="0" x2="1"><stop offset="0" stop-color="#2c2a75"/><stop offset="1" stop-color="#5b3790"/></linearGradient></defs>
    <path d="M0 10L300 35L0 55Z" fill="var(--orange)"/>
    <path d="M0 52L1200 14V440H0Z" fill="url(#svg-g)"/>
  </svg>
  <h2 style="top:105px;color:#fff">Our services</h2>
  <svg class="arrow" style="left:98px;top:215px" viewBox="0 0 40 40"><path d="M26 8L12 20l14 12M12 20h24" stroke="#fff" stroke-width="2.5" fill="none"/></svg>
  <svg class="arrow" style="left:1062px;top:215px" viewBox="0 0 40 40"><path d="M14 8l14 12-14 12M28 20H4" stroke="#fff" stroke-width="2.5" fill="none"/></svg>
  <div class="card" style="left:161px">
    <svg viewBox="0 0 62 62" fill="none" stroke="#fff" stroke-width="2"><rect x="6" y="8" width="50" height="34"/><path d="M20 50h22M31 42v8M18 34V24M26 34V18M34 34V22M42 34V16"/></svg>Financing</div>
  <div class="card" style="left:384px">
    <svg viewBox="0 0 62 62" fill="none" stroke="#fff" stroke-width="2"><rect x="10" y="14" width="42" height="40"/><path d="M18 6h26v8M18 24h10M34 24h10M18 32h10M34 32h10M18 40h10M34 40h10"/></svg>Financial<br>remittances</div>
  <div class="card" style="left:607px">
    <svg viewBox="0 0 62 62" fill="none" stroke="#fff" stroke-width="2"><path d="M14 6h26l10 10v40H14z"/><path d="M20 22h22M20 30h22M20 38h14"/><circle cx="42" cy="46" r="5"/></svg>Documentation</div>
  <div class="card" style="left:830px">
    <svg viewBox="0 0 62 62" fill="none" stroke="#fff" stroke-width="2"><rect x="10" y="16" width="34" height="40"/><path d="M16 24h22M16 34h6M26 34h6M16 42h6M26 42h6M16 50h6M26 50h6"/><circle cx="44" cy="14" r="8"/><path d="M44 10v8M41 14h6"/></svg>Accounting</div>
</section>

<!-- 360 VISION -->
<section class="sec vision">
  <div class="ph" style="inset:0;background:linear-gradient(180deg,#5f7fa8 0%,#3d5578 45%,#2a3a5c 100%)" role="img" aria-label="Harbour city skyline with towers"></div>
  <div class="ph" style="inset:0;background:rgba(40,35,90,.45)"></div>
  <h2>360º VISION</h2>
  <p>We take care of absolutely everything to make you feel at home in Florida!</p>
  <div class="btn btn-red" style="left:493px;top:229px;width:186px;height:44px;font-size:14px">Click here</div>
  <svg class="ph" style="left:0;bottom:0" width="1200" height="40" viewBox="0 0 1200 40"><path d="M0 40L1200 0V40Z" fill="#fff"/><path d="M0 40L1200 4V0L0 36Z" fill="var(--violet)"/></svg>
</section>

<!-- PROJECTS -->
<section class="sec projects">
  <h2 style="top:56px;color:var(--purple-deep)">Our projects</h2>
  <div class="tile" style="left:161px;top:119px;width:379px;height:200px;background:linear-gradient(135deg,#d9d6cf,#8d8477)" role="img" aria-label="Modern kitchen with island and bar stools"></div>
  <div class="tile" style="left:551px;top:119px;width:194px;height:200px;background:linear-gradient(135deg,#6f8a5a,#8a8f96)" role="img" aria-label="Aerial view of a residential neighbourhood"></div>
  <div class="tile tile-label" style="left:751px;top:119px;width:276px;height:200px;background:linear-gradient(135deg,#5d5a56,#3a3634)" role="img" aria-label="Living room interior">Project title<span>MORE INFO</span></div>
  <div class="tile" style="left:161px;top:331px;width:194px;height:200px;background:linear-gradient(180deg,#bcd0e0,#a7a29a)" role="img" aria-label="Two-storey house facade"></div>
  <div class="tile" style="left:361px;top:331px;width:379px;height:200px;background:linear-gradient(135deg,#4b6a4a,#4aa6c0)" role="img" aria-label="Resort swimming pool with palm trees"></div>
  <div class="tile" style="left:751px;top:331px;width:276px;height:200px;background:linear-gradient(135deg,#6f7d86,#3d7fa8)" role="img" aria-label="Screened patio with private pool"></div>
  <div class="btn" style="left:525px;top:557px;width:186px;height:47px;font-size:14px;background:var(--purple-deep)">View more</div>
</section>

<!-- PRICES -->
<section class="sec prices">
  <div class="ph" style="left:0;top:0;width:1200px;height:476px;background:linear-gradient(180deg,rgba(255,255,255,0),rgba(210,212,220,.6))" role="img" aria-label="Faded skyline above the clouds"></div>
  <svg class="ph" style="left:0;top:0" width="1200" height="60" viewBox="0 0 1200 60"><path d="M840 50L1200 0V26Z" fill="var(--purple)"/><path d="M1000 34L1200 8V14Z" fill="var(--orange)"/></svg>
  <svg class="ph" style="left:190px;top:60px" width="350" height="345" viewBox="0 0 350 345">
    <polygon points="60,40 180,6 300,60 330,200 260,320 120,338 20,250 10,120" fill="var(--violet)"/>
    <polygon points="30,60 150,12 280,40 320,180 270,300 130,330 20,250 12,130" fill="#7ea3cc" role="img" aria-label="City skyline with a pyramid-shaped tower"/>
    <path d="M20 250L130 330L200 322L40 240Z" fill="var(--orange)"/>
  </svg>
  <h2>Receives prices and<br>plants of buildings</h2>
  <p>Have at your disposal information about our properties.<br><br>You will have an always up-to-date list of our available launches and homes.</p>
  <div class="btn btn-orange" style="left:599px;top:316px;width:185px;height:42px;font-size:13px">Request here</div>
</section>

<!-- STATS -->
<section class="sec stats">
  <div class="stat" style="left:165px"><b>40+</b><span>Cities</span></div>
  <div class="stat" style="left:350px"><b>18</b><span>States</span></div>
  <div class="stat" style="left:541px"><b>1954</b><span>Founded in</span></div>
  <div class="stat" style="left:746px"><b>600 MORE THAN</b><span>Condominiums under<br>construction</span></div>
</section>

<!-- BUILDER -->
<section class="sec builder">
  <div class="ph" style="left:0;top:0;width:606px;height:446px;background:linear-gradient(180deg,#8fb6e0 0%,#6b6f78 55%,#4f7a3f 100%)" role="img" aria-label="Two-storey family home with porch and lawn"></div>
  <h2>Halvorsen</h2>
  <p>HALVORSEN HOMES is more than just a real estate developer. It is one of the largest builders in the US. The commitment to quality, value and integrity is the fundamental basis of HALVORSEN. The condominiums built by HALVORSEN cater to all lifestyles.</p>
</section>

<!-- CONTACT -->
<section class="sec contact">
  <div class="ph photo" role="img" aria-label="Family enjoying a sunny day outdoors, purple tint"></div>
  <div class="kicker">We are here to help you</div>
  <h2>What you need</h2>
  <div class="field" style="left:167px;top:138px;width:282px;height:47px">Name</div>
  <div class="field" style="left:461px;top:138px;width:281px;height:47px">Email address</div>
  <div class="field" style="left:754px;top:138px;width:282px;height:47px">Phone Number</div>
  <div class="field msg" style="left:167px;top:197px;width:869px;height:117px">Message</div>
  <div class="btn btn-orange" style="left:499px;top:338px;width:211px;height:47px;font-size:16px">Submit now</div>
</section>

<!-- FOOTER -->
<footer class="sec footer">
  <div class="addr" style="top:66px">
    <b><svg class="pin" viewBox="0 0 10 14"><path d="M5 0a5 5 0 0 1 5 5c0 4-5 9-5 9S0 9 0 5a5 5 0 0 1 5-5z" fill="var(--crimson)"/></svg>Atlântica Center</b>
    3º andar, Rua das Palmeiras 140<br>Botafogo, RJ - Brasil
  </div>
  <div class="addr" style="top:140px">
    <b><svg class="pin" viewBox="0 0 10 14"><path d="M5 0a5 5 0 0 1 5 5c0 4-5 9-5 9S0 9 0 5a5 5 0 0 1 5-5z" fill="var(--crimson)"/></svg>Orlando</b>
    4410 Maple Grove Avenue, Suite 208, Orlando, USA
  </div>
  <div class="addr" style="top:194px;display:flex;align-items:center;gap:6px;font-weight:600;color:var(--purple-deep)">
    <i class="dot" style="background:var(--crimson);border-radius:2px"></i>hello@coralparlor.example
  </div>
  <div class="brand">CORAL<small>PARLOR</small></div>
  <div class="wa" style="left:813px;top:67px;height:30px;font-size:14px">USA +1 (555) 010-2248</div>
  <div class="phones" style="left:790px;top:110px">
    <span><i class="dot" style="background:var(--green)"></i>+55 21 5550-1842</span>
    <span><i class="dot" style="background:var(--purple)"></i>+1 (555) 014-3370</span>
  </div>
  <div class="cta-icon" style="left:769px;top:150px"><i style="background:var(--crimson)"></i>Talk to an<br>agent</div>
  <div class="cta-icon" style="left:913px;top:150px"><i style="background:var(--teal)"></i>Schedule a<br>conversation</div>
</footer>
<div class="sec legal">
  <span>© 2017 - The Coral Parlor</span>
  <nav><span>Home</span><span>Properties</span><span>Magazine</span><span>Contact</span><span>Terms of use</span></nav>
</div>

</body>
</html>
```